New web design for a service provider in the medical field

We are looking for a new design for our website. We are a company that repairs and sells medical endoscopes. Our customers include doctors and hospitals. Our current website can be found at https://lumavex.de/en/lumavex-english.
We need a new web design (without programming) for the following 3 pages:
-Startpage https://lumavex.de/en/lumavex-english/
-Used endoscopes https://lumavex.de/en/used-endoscopes/
-Purchase https://lumavex.de/en/purchase/
The design should be modern and stylish.
The blue color of the logo should be reflected on the page, but not too intrusive.
I have uploaded the images from the header. If more images are needed, let me know and I will upload them.

Target Market(s)
Doctors and hospitals

```html
<!DOCTYPE html>
<html lang="en">
<head>
<meta charset="utf-8">
<title>Lumavex – Purchase</title>
<link href="https://fonts.googleapis.com/css2?family=Outfit:wght@400;500;600;700&family=Barlow:wght@400;500;600&display=swap" rel="stylesheet">
<style>
:root{
  --blue:#29a3dc;
  --blue-light:#bfe3f4;
  --navy:#1c3a52;
  --ink:#1e2d3b;
  --muted:#6b7784;
  --line:#c9d2da;
  --page:#f3f8fb;
  --white:#fff;
}
*{box-sizing:border-box;margin:0;padding:0}
html,body{width:1200px;height:3033px;overflow:hidden}
body{position:relative;background:var(--white);font-family:"Barlow",sans-serif;color:var(--ink)}
.abs{position:absolute}
.heading{font-family:"Outfit",sans-serif;font-weight:700;text-transform:uppercase;color:var(--navy)}

/* header */
.topbar{left:0;top:0;width:1200px;height:42px}
.topbar-info{right:60px;top:0;height:42px;display:flex;align-items:center;gap:24px;color:var(--white);font-family:"Outfit",sans-serif;font-size:13px;font-weight:600}
.topbar-info span{display:flex;align-items:center;gap:7px}
.ico{width:20px;height:20px;border-radius:50%;background:var(--white);display:inline-flex;align-items:center;justify-content:center}
.brand{left:92px;top:20px;width:160px;height:110px;border-radius:0 0 80px 80px;background:var(--white);display:flex;align-items:center;justify-content:center;gap:8px}
.brand-dot{width:12px;height:12px;border-radius:50%;background:var(--blue)}
.brand-name{font-family:"Outfit",sans-serif;font-weight:600;font-size:24px;color:var(--navy)}
.nav{left:300px;top:68px;display:flex;gap:0;font-family:"Outfit",sans-serif;font-weight:600;font-size:12.5px;color:var(--navy)}
.nav a{color:inherit;text-decoration:none;margin-right:28px;padding-bottom:8px}
.nav a.active{border-bottom:2px solid var(--blue)}

/* hero */
.hero{left:0;top:113px;width:1200px;height:560px;background:linear-gradient(90deg,#dfecf3 0%,#e9f0f4 45%,#eef1f3 100%)}
.hero-photo{left:520px;top:113px;width:680px;height:480px;background:radial-gradient(ellipse at 55% 55%,#3a3d42 0%,#6c7178 28%,rgba(220,226,230,0) 62%)}
.hero-kicker{left:103px;top:276px;font-family:"Outfit",sans-serif;font-size:27px;color:var(--blue);text-transform:uppercase}
.hero-title{left:102px;top:308px;font-size:44px;line-height:47px}
.divider-arrow{width:76px;height:76px;border-radius:50%;background:var(--white);border:2px solid var(--blue-light);display:flex;align-items:center;justify-content:center}

/* sell section */
.sell-ring{left:104px;top:702px;width:452px;height:452px;border-radius:50%;border:2px solid #a6d8ef}
.sell-photo{left:128px;top:728px;width:400px;height:400px;border-radius:50%;background:radial-gradient(circle at 55% 55%,#5b5f64 0%,#9ea3a8 45%,#d3d6d8 100%);box-shadow:0 0 0 10px var(--white),0 0 0 12px #a6d8ef}
.sell-title{left:589px;top:734px;font-size:33px;line-height:39px}
.sell-title em{font-style:normal;color:var(--blue)}
.sell-rule{left:589px;top:860px;width:80px;height:2px;background:var(--blue)}
.sell-text{left:592px;top:884px;width:505px;font-family:"Outfit",sans-serif;font-size:17.5px;line-height:27.3px;color:#2a3642}
.sell-text p+p{margin-top:11px}

/* replace section */
.replace{left:0;top:1227px;width:1200px;height:510px;background:linear-gradient(180deg,#1f4663 0%,#21577a 60%,#245f84 100%)}
.replace-title{left:0;top:1318px;width:1200px;text-align:center;color:var(--white);font-size:34px;line-height:36px}
.replace-rule{left:562px;top:1402px;width:72px;height:2px;background:var(--blue)}
.replace-text{left:225px;top:1424px;width:750px;text-align:center;color:var(--white);font-family:"Outfit",sans-serif;font-size:18px;line-height:22px}
.btn{background:var(--blue);color:var(--white);font-family:"Outfit",sans-serif;font-weight:600;border-radius:30px;display:flex;align-items:center;justify-content:center}
.replace-btn{left:400px;top:1504px;width:410px;height:52px;font-size:17px}

/* form */
.form-bg{left:0;top:1737px;width:1200px;height:880px;background:var(--page)}
.card{left:104px;top:1820px;width:1024px;height:727px;background:var(--white);border:1px solid #e2e9ee;border-radius:6px}
.card > *{position:absolute}
.card h3{font-family:"Outfit",sans-serif;font-weight:600;font-size:21px;color:var(--navy)}
.lbl{font-family:"Barlow",sans-serif;font-weight:500;font-size:14.5px;color:var(--ink)}
.field{border:1px solid var(--line);border-radius:2px;font-size:15px;color:#4e5a66;display:flex;align-items:center;padding:0 18px;justify-content:space-between}
.rule{left:45px;top:374px;width:933px;height:1px;background:#dde4ea}
.note{font-size:11px;font-style:italic;color:#4e5a66}
.consent{left:67px;top:567px;width:880px;font-size:11.5px;line-height:19px;color:#3b4753}
.check{left:51px;top:570px;width:22px;height:18px;border:1px solid var(--line)}
.browse{border:1px solid var(--blue);border-radius:16px;font-size:13px;font-weight:600;color:var(--navy);padding:5px 14px;display:flex;gap:6px;align-items:center}

/* footer */
.foot-brand{left:130px;top:2740px;display:flex;align-items:center;gap:8px}
.foot-about{left:126px;top:2846px;width:270px;font-family:"Outfit",sans-serif;font-size:13.5px;line-height:15px;color:var(--muted)}
.foot-col{top:2740px;border-left:3px solid var(--blue);padding-left:16px;height:170px}
.foot-col h4{font-family:"Outfit",sans-serif;font-weight:600;font-size:15.5px;color:var(--navy);margin-bottom:16px;margin-top:6px}
.foot-col li{list-style:none;font-family:"Outfit",sans-serif;font-size:14.5px;color:#3b4753;margin-bottom:11px}
.vsep{top:2700px;width:1px;height:200px;background:#eef1f3}
.social{display:flex;gap:8px}
.social i{display:block;width:28px;height:28px;border-radius:50%;background:var(--navy)}
.foot-line{left:0;top:2968px;width:1200px;height:1px;background:#dfe4e8}
.copy{left:0;top:2988px;width:1200px;text-align:center;font-size:13px;color:var(--muted)}
</style>
</head>
<body>

<!-- header -->
<svg class="abs topbar" width="1200" height="42" viewBox="0 0 1200 42"><path d="M671 0H1200V42H706Z" fill="#29a3dc"/></svg>
<div class="abs topbar-info">
  <span><i class="ico"><svg width="12" height="9" viewBox="0 0 12 9"><path d="M0 0H12V9H0Z M0 0L6 5L12 0" fill="none" stroke="#29a3dc" stroke-width="1.5"/></svg></i>info@lumavex.de</span>
  <span><i class="ico"><svg width="11" height="11" viewBox="0 0 24 24"><path d="M6.6 10.8a15 15 0 006.6 6.6l2.2-2.2c.3-.3.7-.4 1-.2 1.1.4 2.3.6 3.6.6.6 0 1 .4 1 1V20c0 .6-.4 1-1 1A17 17 0 013 4c0-.6.4-1 1-1h3.5c.6 0 1 .4 1 1 0 1.3.2 2.5.6 3.6.1.3 0 .7-.2 1z" fill="#29a3dc"/></svg></i>+49 4000 555 120-0</span>
  <span>ENG <svg width="9" height="6" viewBox="0 0 9 6"><path d="M1 1l3.5 3.5L8 1" stroke="#fff" fill="none" stroke-width="1.5"/></svg></span>
</div>
<div class="abs brand"><i class="brand-dot"></i><span class="brand-name">Lumavex</span></div>
<nav class="abs nav">
  <a class="active" href="#">ENDOSCOPE REPAIR</a>
  <a href="#">ENDOSCOPY SYSTEMS</a>
  <a href="#">ENDOSCOPY ACCESSORIES ⌄</a>
  <a href="#" style="margin-right:42px">ACCESSORIES CATALOG</a>
  <a href="#">PURCHASE</a>
</nav>

<!-- hero -->
<div class="abs hero"></div>
<div class="abs hero-photo" role="img" aria-label="Photograph of a video endoscope control head and insertion tube on a light surface"></div>
<div class="abs hero-kicker">Purchase endoscopes</div>
<h1 class="abs heading hero-title">Sustainable and<br>economical</h1>
<svg class="abs" style="left:0;top:555px" width="1200" height="110" viewBox="0 0 1200 110">
  <path d="M0 4L603 62L0 106Z" fill="#29a3dc"/>
  <path d="M1200 10L603 62L1200 110Z" fill="#1c3a52"/>
  <path d="M0 106L603 62L1200 110Z" fill="#fff"/>
</svg>
<div class="abs divider-arrow" style="left:565px;top:580px"><svg width="22" height="28" viewBox="0 0 22 28"><path d="M11 2V25M2 16l9 9 9-9" fill="none" stroke="#29a3dc" stroke-width="2"/></svg></div>

<!-- sell -->
<div class="abs sell-ring"></div>
<div class="abs sell-photo" role="img" aria-label="Close-up photograph of an endoscope shaft and connector"></div>
<h2 class="abs heading sell-title">Do you want to sell<br>your endoscope?<br><em>You are at the right adress!</em></h2>
<div class="abs sell-rule"></div>
<div class="abs sell-text">
  <p>We are always interested in buying used endoscopes, accessories and peripherals from Orvanta, Pentrix and Fujara at fair conditions. We can promise you an objective offer with a clear conscience! Use the form below to offer us your device! If you want to have several devices checked, one of our technicians will usually come to you for the check. We also check defective and incomplete devices!</p>
  <p>We would be happy to take a look at your device!</p>
</div>

<!-- replace -->
<div class="abs replace" role="img" aria-label="Blue-tinted photograph of endoscopy equipment and cables"></div>
<h2 class="abs heading replace-title" style="color:#fff">Are you looking to replace your<br>for sale device?</h2>
<div class="abs replace-rule"></div>
<p class="abs replace-text">Lorem ipsum dolor sit amet, consectetur adipiscing elit, sed do eiusmod tempor incididunt ut labore et dolore magna aliqua. Ut enim ad minim veniam.</p>
<div class="abs btn replace-btn">Browse our range of excellent used equipment!</div>
<svg class="abs" style="left:0;top:1630px" width="1200" height="112" viewBox="0 0 1200 112">
  <path d="M0 6L609 66L0 108Z" fill="#29a3dc"/>
  <path d="M1200 4L609 66L1200 112Z" fill="#bfe3f4"/>
  <path d="M0 108L609 66L1200 112V112H0Z" fill="#f3f8fb"/>
</svg>
<div class="abs divider-arrow" style="left:578px;top:1665px;width:62px;height:62px"><svg width="18" height="22" viewBox="0 0 18 22"><path d="M9 1V20M2 13l7 7 7-7" fill="none" stroke="#29a3dc" stroke-width="2"/></svg></div>

<!-- form -->
<div class="abs form-bg" style="top:1742px"></div>
<form class="abs card">
  <h3 style="left:42px;top:40px">Personal Information</h3>
  <h3 style="left:532px;top:50px">Informations about the device</h3>

  <span class="lbl" style="left:45px;top:94px">Salutation *</span>
  <span class="lbl" style="left:269px;top:94px">co. / dr. off. *</span>
  <span class="lbl" style="left:532px;top:95px">Brand *</span>
  <span class="lbl" style="left:746px;top:95px">Model*</span>
  <div class="field" style="left:42px;top:120px;width:217px;height:48px">Choose <svg width="14" height="8" viewBox="0 0 14 8"><path d="M1 1l6 6 6-6" fill="none" stroke="#1e2d3b" stroke-width="2"/></svg></div>
  <div class="field" style="left:266px;top:120px;width:225px;height:48px">Company / doctor office</div>
  <div class="field" style="left:532px;top:121px;width:202px;height:48px">Choose <svg width="14" height="8" viewBox="0 0 14 8"><path d="M1 1l6 6 6-6" fill="none" stroke="#1e2d3b" stroke-width="2"/></svg></div>
  <div class="field" style="left:743px;top:121px;width:238px;height:48px">Choose</div>

  <span class="lbl" style="left:47px;top:190px">Surname *</span>
  <span class="lbl" style="left:271px;top:193px">First name*</span>
  <span class="lbl" style="left:534px;top:180px">Asking Price *</span>
  <div class="field" style="left:45px;top:218px;width:218px;height:42px"></div>
  <div class="field" style="left:271px;top:218px;width:218px;height:42px"></div>
  <div class="field" style="left:535px;top:208px;width:445px;height:48px"></div>

  <span class="lbl" style="left:43px;top:271px">Email *</span>
  <span class="lbl" style="left:263px;top:271px">Telephone*</span>
  <span class="lbl" style="left:535px;top:265px">Defects / damage</span>
  <div class="field" style="left:43px;top:294px;width:218px;height:43px"></div>
  <div class="field" style="left:267px;top:294px;width:218px;height:43px"></div>
  <div class="field" style="left:533px;top:292px;width:445px;height:48px"></div>

  <div class="rule"></div>

  <h3 style="left:44px;top:398px">Remarks and picture</h3>
  <span class="lbl" style="left:47px;top:442px">Remarks and picture</span>
  <div class="field" style="left:45px;top:470px;width:445px;height:75px;align-items:flex-start;padding-top:12px">Description of the error, other information etc</div>
  <span class="lbl" style="left:529px;top:447px">Upload picture</span>
  <div class="field" style="left:529px;top:472px;width:445px;height:51px;color:#8a95a0">Drag &amp; drop you picture here or
    <span class="browse"><svg width="13" height="13" viewBox="0 0 13 13"><path d="M6.5 9V1M3 4.5l3.5-3.5L10 4.5M1 8v4h11V8" fill="none" stroke="#29a3dc" stroke-width="1.4"/></svg>Browse</span></div>
  <span class="note" style="left:534px;top:535px">allowed formats: jpg, jpeg, png or bmp maximum file size: 4 MB</span>

  <div class="check"></div>
  <p class="consent">I have read the privacy policy and accept it. I agree above input will be transmitted to Lumavex GmbH to get in contact with me respectively to process my request and store all needed informations. Neither a transfer to third parties will happen, nor a use for advertising purposes by Lumavex GmbH!</p>

  <div class="btn" style="left:44px;top:637px;width:158px;height:48px;font-size:17px">SEND</div>
</form>

<!-- footer -->
<svg class="abs" style="left:0;top:2588px" width="1200" height="112" viewBox="0 0 1200 112">
  <path d="M0 0L611 62L0 104Z" fill="#29a3dc"/>
  <path d="M1200 2L611 62L1200 108Z" fill="#1c3a52"/>
  <path d="M0 104L611 62L1200 108V112H0Z" fill="#fff"/>
</svg>
<div class="abs divider-arrow" style="left:581px;top:2620px;width:60px;height:60px"><svg width="18" height="22" viewBox="0 0 18 22"><path d="M9 21V2M2 9l7-7 7 7" fill="none" stroke="#29a3dc" stroke-width="2"/></svg></div>

<div class="abs foot-brand"><i class="brand-dot"></i><span class="brand-name">Lumavex</span></div>
<p class="abs foot-about">Lorem ipsum dolor sit amet, consectetur adipiscing elit, sed do eiusmod tempor incididunt ut labore et dolore</p>

<div class="abs vsep" style="left:468px"></div>
<div class="abs vsep" style="left:708px"></div>
<div class="abs vsep" style="left:914px"></div>

<div class="abs foot-col" style="left:468px">
  <h4>NAVIGATION</h4>
  <ul><li>Home</li><li>Endoscope Repair</li><li>Used Endoscope</li><li>Endoscopy Systems</li></ul>
</div>
<div class="abs foot-col" style="left:708px">
  <h4>RESOURCES</h4>
  <ul><li>Endoscopy Accesories</li><li>Purchase</li><li>Contact Us</li></ul>
</div>
<div class="abs foot-col" style="left:914px">
  <h4>FOLLOW US</h4>
  <div class="social" aria-label="Social media links"><i></i><i></i><i></i><i></i></div>
</div>

<div class="abs foot-line"></div>
<p class="abs copy">© 2022 Lumavex GmbH</p>

</body>
</html>
```